birchwell hollow cattle company website

we would like a home page, an about us page, a page for sires, a page for dams, A sale page where we can list progreny for sale and a contact us. on the about us page we would like there to be a family picture. on the sires page we would like to have a picture of each sire, a description beside them and a link to their online profile at northern hereford registry. on the dam page we would like to have a picture of each dam, aswell as a description beside them aswell as a link to the northern hereford registry site. would like the website to very mobile phone friendly as expecting most traffic to be on phone. we would like the website to look and feel very mich like a farm, rustic, barbed wire and other farm feels. we would also like a frozen genetics pages where we can include pictures and descriptions of the sires and dams aswell as a price for embryos and semen. we need to website to be easy to maintain so we can update pictures and information as it changes, we would like there to be a feature so that people can sign up to be on our mailing list by giving us their mailing addess and email and full name
aswell as an area where they can send us a message to contact us.

leaving for work for 3 weeks in the canadian arctic will have limited ability to use the internet

Target Market(s)

other ranchers, farmers, cattlemen,

Industry/Entity Type

farming, agriculture, cattle

Coding

Coded - Design and coding required

Requirements
Must have
• about page, contact page, sires page, dams page, SALE page.
Nice to have
• country/farm vibe, barbed wire, wood,

```html
<!DOCTYPE html>
<html lang="en">
<head>
<meta charset="utf-8">
<title>Birchwell Hollow Cattle Company</title>
<link href="https://fonts.googleapis.com/css2?family=Crimson+Pro:ital,wght@0,400;0,500;0,600;0,700;1,400&family=Playfair+Display:ital,wght@1,700;1,800&family=Oswald:wght@600&display=swap" rel="stylesheet">
<style>
:root{
  --cream:#f9f6f2;
  --sand:#f3efea;
  --rust:#c0601a;
  --navy:#14213d;
  --ink:#2b2b2b;
  --slate:#4a5060;
  --bark:#231812;
  --bark-2:#2e1c12;
  --rule:#e3c2a8;
  --white:#ffffff;
}
*{box-sizing:border-box;margin:0;padding:0}
html,body{width:1200px;height:2970px;overflow:hidden}
body{font-family:"Crimson Pro",Georgia,serif;background:var(--cream);color:var(--ink);position:relative}
a{text-decoration:none;color:inherit}

/* Header */
.site-header{position:absolute;top:0;left:0;width:1200px;height:83px;background:var(--cream);border-bottom:1px solid #e6ddd3;display:flex;align-items:center;padding:0 30px 0 35px;justify-content:space-between}
.brand{display:flex;align-items:center;gap:10px;font-family:"Oswald",sans-serif;font-weight:600;font-size:19px;color:#111;letter-spacing:.5px;text-transform:uppercase;width:240px;line-height:1.05}
.brand-mark{width:14px;height:14px;background:#111;flex:none}
.main-nav{display:flex;gap:38px;font-size:16px;color:#222;position:absolute;left:486px}
.btn{display:inline-flex;align-items:center;justify-content:center;font-family:"Crimson Pro",serif;font-weight:700;border-radius:6px}
.btn-rust{background:var(--rust);color:#fff;box-shadow:0 3px 8px rgba(0,0,0,.18)}
.header-cta{width:118px;height:37px;font-size:16px}

/* Hero */
.hero{position:absolute;top:83px;left:0;width:1200px;height:606px;background:linear-gradient(180deg,#8a6a44 0%,#a87a46 14%,#7d6a55 32%,#6d6456 55%,#6a6a5a 78%,#6f7560 100%);text-align:center;color:#fff}
.hero h1{font-family:"Playfair Display",serif;font-style:italic;font-weight:800;font-size:72px;margin-top:160px;letter-spacing:-.5px;text-shadow:0 2px 10px rgba(0,0,0,.25)}
.hero p{font-size:22px;line-height:30px;margin-top:14px;color:#f0ebe4;font-weight:400}
.hero-actions{display:flex;justify-content:center;gap:16px;margin-top:42px}
.hero-actions .btn{height:58px;font-size:17px}
.hero-actions .btn-rust{width:170px}
.btn-ghost{width:204px;border:2px solid #fff;color:#fff;background:rgba(255,255,255,.1)}

/* Legacy */
.legacy{position:absolute;top:689px;left:0;width:1200px;height:820px}
.legacy-frame{position:absolute;left:10px;top:82px;width:560px;height:680px;border:1px solid var(--rule);border-radius:14px;transform:rotate(3deg)}
.legacy-photo{position:absolute;left:30px;top:90px;width:539px;height:673px;border-radius:6px;background:linear-gradient(180deg,#c9d6d8 0%,#b6c3c4 28%,#7a4a2d 42%,#6a341c 65%,#b99a66 85%,#c6a36a 100%);box-shadow:0 18px 30px rgba(0,0,0,.18)}
.legacy-copy{position:absolute;left:630px;top:224px;width:540px}
.eyebrow{font-size:14px;font-weight:700;letter-spacing:3px;color:var(--rust)}
.legacy-copy h2{font-family:"Playfair Display",serif;font-style:italic;font-weight:800;font-size:46px;color:var(--navy);margin-top:14px}
.legacy-copy .lead{font-size:19px;line-height:30.5px;color:#3a3f4a;margin-top:30px}
.legacy-copy blockquote{border-left:3px solid #e4b79a;padding:0 0 0 24px;margin-top:28px;font-style:italic;font-size:17px;line-height:27px;color:var(--slate)}
.legacy-rule{margin-top:48px;height:1px;width:538px;background:var(--rule)}
.text-link{display:inline-flex;align-items:center;gap:8px;color:var(--rust);font-weight:700;font-size:16px}
.legacy-copy .text-link{margin-top:40px;letter-spacing:.3px}

.section-rule{position:absolute;top:1550px;left:0;width:1170px;height:1px;background:var(--rule)}

/* Cards */
.offerings{position:absolute;top:1650px;left:31px;width:1138px;display:flex;gap:32px}
.card{width:358px;height:433px;background:#fff;border-radius:8px;box-shadow:0 4px 14px rgba(0,0,0,.07);overflow:hidden}
.card-photo{height:269px}
.photo-sires{background:linear-gradient(180deg,#c7dbe6 0%,#9a5a2e 35%,#8a4a24 62%,#5e9a3c 78%,#4c8a30 100%)}
.photo-dams{background:linear-gradient(180deg,#3f5a2c 0%,#8b8a7a 30%,#9a5a30 55%,#6a9a40 78%,#5a8c34 100%)}
.photo-sales{background:linear-gradient(180deg,#5e90c4 0%,#9cbbd6 25%,#7a8a50 40%,#a8522a 58%,#a07048 80%,#9a6c48 100%)}
.card-body{padding:20px 23px}
.card h3{font-size:24px;font-weight:700;color:#1a1a1a}
.card p{font-size:15px;line-height:23px;color:#555b66;margin-top:10px;max-width:278px}
.card .text-link{margin-top:16px;font-size:16px}

/* Newsletter */
.newsletter-band{position:absolute;top:2159px;left:0;width:1200px;height:377px;background:var(--sand)}
.newsletter{position:absolute;left:30px;top:75px;width:1139px;height:226px;border-radius:24px;background:radial-gradient(circle at 88% 15%,#4a2a18 0%,var(--bark-2) 35%,#201510 100%);box-shadow:0 12px 24px rgba(0,0,0,.2);color:#fff}
.newsletter h2{position:absolute;left:91px;top:56px;font-size:37px;font-weight:700}
.newsletter p{position:absolute;left:91px;top:118px;width:400px;font-size:17px;line-height:26px;color:#e6ddd3}
.signup{position:absolute;left:629px;top:79px;display:flex;height:52px}
.signup-input{width:278px;height:52px;background:#fff;border-radius:6px 0 0 6px;display:flex;align-items:center;padding-left:22px;font-size:15px;color:#777}
.signup-btn{width:142px;height:52px;background:var(--rust);border-radius:0 6px 6px 0;display:flex;align-items:center;justify-content:center;font-weight:700;font-size:14px;letter-spacing:1.8px;color:#fff}

/* Footer */
.site-footer{position:absolute;top:2536px;left:0;width:1200px;height:434px;background:var(--bark);color:#d8cfc6}
.footer-cols{position:absolute;left:30px;top:62px;display:flex}
.footer-col{width:296px}
.footer-brand{display:flex;align-items:center;gap:10px;font-size:19px;font-weight:700;color:#fff;letter-spacing:.3px}
.footer-brand .dot{width:16px;height:16px;border-radius:50%;background:var(--rust);flex:none}
.footer-tag{font-style:italic;font-size:15px;line-height:24px;color:#a89d93;margin-top:18px;width:250px}
.footer-col h4{font-size:15px;font-weight:700;letter-spacing:1.3px;color:var(--rust)}
.footer-col ul{list-style:none;margin-top:26px}
.footer-col li{font-size:15px;line-height:17px;color:#b8ada3;margin-bottom:20px}
.contact-line{display:flex;gap:10px;font-size:16px;color:#b8ada3;line-height:23px;margin-top:24px}
.contact-line + .contact-line{margin-top:14px}
.footer-rule{position:absolute;left:30px;top:300px;width:1139px;height:1px;background:#3a2c24}
.copyright{position:absolute;top:332px;width:1200px;text-align:center;font-size:13px;color:#7f746b}
</style>
</head>
<body>

<header class="site-header">
  <a class="brand" href="#"><span class="brand-mark"></span>Birchwell Hollow<br>Cattle Company</a>
  <nav class="main-nav">
    <a href="#">Home</a><a href="#">Sires</a><a href="#">Dams</a><a href="#">Sales</a><a href="#">Contact</a>
  </nav>
  <a class="btn btn-rust header-cta" href="#">View Sales</a>
</header>

<section class="hero" role="img" aria-label="Photo of cattle standing behind a wire fence at sunset">
  <h1>Legacy in Every Breed</h1>
  <p>Welcome to Birchwell Hollow Ranch, where tradition meets superior genetics.<br>Experience our commitment to quality cattle.</p>
  <div class="hero-actions">
    <a class="btn btn-rust" href="#">Meet Our Sires</a>
    <a class="btn btn-ghost" href="#">View Current Sales</a>
  </div>
</section>

<section class="legacy">
  <div class="legacy-frame"></div>
  <div class="legacy-photo" role="img" aria-label="Photo of a red bull standing on straw beside steel pen rails"></div>
  <div class="legacy-copy">
    <div class="eyebrow">EST. 1954</div>
    <h2>Our Ranch Legacy</h2>
    <p class="lead">For generations, our family has dedicated itself to the craft of raising superior cattle. Located in the heart of the countryside, our ranch combines traditional values with modern genetics.</p>
    <blockquote>"Our commitment to excellence is rooted in the soil we walk upon and the legacy we leave behind. Every animal is raised with meticulous care for superior results."</blockquote>
    <div class="legacy-rule"></div>
    <a class="text-link" href="#">LEARN MORE ABOUT OUR HISTORY
      <svg width="20" height="12" viewBox="0 0 20 12"><path d="M1 6h17M13 1l5 5-5 5" fill="none" stroke="currentColor" stroke-width="2"/></svg></a>
  </div>
</section>

<div class="section-rule"></div>

<section class="offerings">
  <article class="card">
    <div class="card-photo photo-sires" role="img" aria-label="Photo of a red herd bull on green pasture"></div>
    <div class="card-body">
      <h3>Superior Sires</h3>
      <p>View our elite herd bulls with proven track records and exceptional growth rates.</p>
      <a class="text-link" href="#">View Sires <svg width="16" height="14" viewBox="0 0 16 14"><path d="M1 7h13M9 2l5 5-5 5" fill="none" stroke="currentColor" stroke-width="2"/></svg></a>
    </div>
  </article>
  <article class="card">
    <div class="card-photo photo-dams" role="img" aria-label="Photo of a red cow with her calf in a grassy paddock"></div>
    <div class="card-body">
      <h3>Proven Dams</h3>
      <p>Explore our foundation females selected for maternal excellence and longevity.</p>
      <a class="text-link" href="#">View Dams <svg width="16" height="14" viewBox="0 0 16 14"><path d="M1 7h13M9 2l5 5-5 5" fill="none" stroke="currentColor" stroke-width="2"/></svg></a>
    </div>
  </article>
  <article class="card">
    <div class="card-photo photo-sales" role="img" aria-label="Photo of red cattle gathered in a steel pen under a blue sky"></div>
    <div class="card-body">
      <h3>Current Sales</h3>
      <p>Browse our currently available livestock including yearlings and replacement heifers.</p>
      <a class="text-link" href="#">Shop Now <svg width="20" height="18" viewBox="0 0 20 18"><path d="M1 1h3l2.5 10h10L19 4H5.5" fill="none" stroke="currentColor" stroke-width="1.8" stroke-linejoin="round"/><circle cx="8" cy="15" r="1.6" fill="currentColor"/><circle cx="15" cy="15" r="1.6" fill="currentColor"/></svg></a>
    </div>
  </article>
</section>

<section class="newsletter-band">
  <div class="newsletter">
    <h2>Stay Informed</h2>
    <p>Join our inner circle for exclusive updates on new genetics and upcoming seasonal sales.</p>
    <form class="signup">
      <div class="signup-input">Your email address</div>
      <div class="signup-btn">JOIN NOW</div>
    </form>
  </div>
</section>

<footer class="site-footer">
  <div class="footer-cols">
    <div class="footer-col">
      <div class="footer-brand"><span class="dot"></span>BIRCHWELL HOLLOW RANCH</div>
      <p class="footer-tag">"Preserving tradition, perfecting genetics. Since 1954."</p>
    </div>
    <div class="footer-col">
      <h4>QUICK LINKS</h4>
      <ul><li>About Us</li><li>Our Sires</li><li>Available Dams</li><li>Privacy Policy</li></ul>
    </div>
    <div class="footer-col">
      <h4>CONTACT US</h4>
      <div class="contact-line">
        <svg width="16" height="20" viewBox="0 0 16 20"><path d="M8 1a6.5 6.5 0 0 0-6.5 6.5C1.5 12 8 19 8 19s6.5-7 6.5-11.5A6.5 6.5 0 0 0 8 1z" fill="none" stroke="#c0601a" stroke-width="1.6"/><circle cx="8" cy="7.5" r="2.3" fill="none" stroke="#c0601a" stroke-width="1.6"/></svg>
        <span>88 Willow Bend Road,<br>Alder Flats, TX 75990</span>
      </div>
      <div class="contact-line">
        <svg width="18" height="18" viewBox="0 0 18 18"><path d="M3 1.5h3l1.5 4-2 1.3a9 9 0 0 0 5.7 5.7l1.3-2 4 1.5v3a1.5 1.5 0 0 1-1.5 1.5A14.5 14.5 0 0 1 1.5 3 1.5 1.5 0 0 1 3 1.5z" fill="none" stroke="#c0601a" stroke-width="1.6" stroke-linejoin="round"/></svg>
        <span>(555) 804-2219</span>
      </div>
    </div>
    <div class="footer-col">
      <h4>FOLLOW US</h4>
    </div>
  </div>
  <div class="footer-rule"></div>
  <p class="copyright">© 2024 Birchwell Hollow Ranch. All rights reserved. Designed for the future of ranching.</p>
</footer>

</body>
</html>
```